Melorix artwork for new single release

I need Melorix artwork creating to release a new single on there.

The specs are:

Ideal size: 3000 x 3000 pixels
Minimum size: 1400 x 1400 pixels
Aspect ratio: 1:1 (must be a perfect square)
File format: JPG or PNG
Color space: sRGB
File size: Max 4MB

The song is called "Was It Ever Rain?"
The artist is "Martin Hollow"

We have no images of Martin, so it really is open to imagination.

Target Market(s)

Melorix listeners

Industry/Entity Type

Music

```html
<!DOCTYPE html>
<html lang="en">
<head>
<meta charset="utf-8">
<title>Was It Ever Rain? – Martin Hollow</title>
<link rel="stylesheet" href="https://fonts.googleapis.com/css2?family=Montserrat:wght@500;700&display=swap">
<style>
  :root {
    --backdrop: #e6e6e6;
    --card: #ffffff;
    --ink: #000000;
    --heart: #e3202b;
    --art-skin: #e9c4b4;
    --art-red: #f2483b;
    --art-blue: #1f64b3;
    --art-cyan: #1a9ac9;
    --art-yellow: #e8d64a;
    --art-hair: #1b1410;
  }
  html, body {
    margin: 0;
    padding: 0;
    width: 1200px;
    height: 2400px;
    overflow: hidden;
    background: var(--backdrop);
    font-family: "Montserrat", Arial, sans-serif;
  }
  .canvas {
    position: relative;
    width: 1200px;
    height: 2400px;
  }
  .player-card {
    position: absolute;
    left: 260px;
    top: 131px;
    width: 681px;
    height: 939px;
    background: var(--card);
    box-shadow: 0 14px 40px rgba(0, 0, 0, 0.35);
  }
  .cover-art {
    position: absolute;
    left: 65px;
    top: 67px;
    width: 552px;
    height: 552px;
    background:
      linear-gradient(160deg, transparent 55%, var(--art-hair) 80%),
      linear-gradient(115deg, var(--art-skin) 0%, var(--art-red) 28%, var(--art-cyan) 40%, var(--art-yellow) 52%, var(--art-blue) 66%, var(--art-blue) 80%, var(--art-hair) 100%);
  }
  .track-title {
    position: absolute;
    left: 67px;
    top: 670px;
    margin: 0;
    font-size: 27px;
    font-weight: 700;
    letter-spacing: 0.5px;
    color: var(--ink);
  }
  .track-artist {
    position: absolute;
    left: 68px;
    top: 708px;
    margin: 0;
    font-size: 21px;
    font-weight: 500;
    letter-spacing: 0.4px;
    color: var(--ink);
  }
  .like-icon {
    position: absolute;
    left: 576px;
    top: 700px;
    width: 34px;
    height: 32px;
  }
  .progress {
    position: absolute;
    left: 65px;
    top: 745px;
    width: 554px;
    height: 20px;
  }
  .controls {
    position: absolute;
    left: 0;
    top: 790px;
    width: 681px;
    height: 110px;
  }
  .detail-art {
    position: absolute;
    left: 0;
    top: 1200px;
    width: 1200px;
    height: 1200px;
    background:
      linear-gradient(160deg, transparent 55%, var(--art-hair) 82%),
      linear-gradient(115deg, var(--art-skin) 0%, var(--art-red) 28%, var(--art-cyan) 40%, var(--art-yellow) 52%, var(--art-blue) 66%, var(--art-blue) 80%, var(--art-hair) 100%);
  }
</style>
</head>
<body>
<main class="canvas">
  <section class="player-card">
    <div class="cover-art" role="img" aria-label="Close-up portrait with bold geometric face paint in red, cyan, yellow, pink and a blue painted ear"></div>
    <h1 class="track-title">Was It Ever Rain?</h1>
    <p class="track-artist">Martin Hollow</p>
    <svg class="like-icon" viewBox="0 0 34 32" aria-label="Liked">
      <path fill="var(--heart)" d="M17 31 C 6 22 0 16 0 9 C 0 4 4 0 9 0 C 12.5 0 15.5 2 17 5 C 18.5 2 21.5 0 25 0 C 30 0 34 4 34 9 C 34 16 28 22 17 31 Z"/>
    </svg>
    <svg class="progress" viewBox="0 0 554 20" aria-label="Playback progress">
      <line x1="0" y1="10" x2="554" y2="10" stroke="var(--ink)" stroke-width="3.5" stroke-linecap="round"/>
      <circle cx="275" cy="10" r="10" fill="var(--ink)"/>
    </svg>
    <svg class="controls" viewBox="0 0 681 110" aria-label="Playback controls">
      <g class="shuffle" fill="none" stroke="var(--ink)" stroke-width="3.5" stroke-linecap="round" stroke-linejoin="round">
        <path d="M60 42 H70 C82 42 86 68 98 68 H118"/>
        <path d="M60 68 H70 C82 68 86 42 98 42 H118"/>
        <path d="M111 35 L118 42 L111 49"/>
        <path d="M111 61 L118 68 L111 75"/>
      </g>
      <g class="previous" fill="var(--ink)">
        <rect x="186" y="35" width="5" height="40"/>
        <path d="M194 55 L224 35 V75 Z"/>
      </g>
      <g class="play">
        <circle cx="340" cy="55" r="49" fill="none" stroke="var(--ink)" stroke-width="4"/>
        <path d="M324 38 L358 55 L324 72 Z" fill="var(--ink)"/>
      </g>
      <g class="next" fill="var(--ink)">
        <path d="M473 35 L503 55 L473 75 Z"/>
        <rect x="505" y="35" width="5" height="40"/>
      </g>
      <g class="repeat" fill="none" stroke="var(--ink)" stroke-width="3.5" stroke-linecap="round" stroke-linejoin="round">
        <path d="M581 60 V50 C581 44 585 41 591 41 H631"/>
        <path d="M625 34 L632 41 L625 48"/>
        <path d="M641 50 V60 C641 66 637 69 631 69 H591"/>
        <path d="M597 62 L590 69 L597 76"/>
      </g>
    </svg>
  </section>
  <div class="detail-art" role="img" aria-label="Enlarged detail of the cover artwork: geometric face paint stripes around the eye and a blue painted ear"></div>
</main>
</body>
</html>
```